WP website design (Tarnwick)

We need a wordpress design for an established auction and real estate company based in Arkansas. The winning design will incorporate a professional color scheme with company logo in a clean layout. The design needs to consider that this will be developed on a responsive theme.

Industry/Entity Type

Real Estate

Font styles to use
Sans Serif

Colors

Designer to choose colors to be used in the design.

Requirements
Must have
• Site will have slideshow, please use stock real estate or other image. A rough idea of homepage content is attached - not necessarily for design purposes.

Navigation Structure is:
1) Home
2) Auctions
3) Services
4) For Sale
5) About Us
6) Ned Videos
7) News & Events
8) Contact Us

Widgets will include:
Social media icons (Facebook, Youtube, RSS)
Testimonials Widget - this should be prominent
Featured Video
Email Signup form (Sign up to receive exclusive email updates for Tarnwick auctions. )
Nice to have
• A drop down menu example
Should not have
• no gavel in the design

```html
<!DOCTYPE html>
<html lang="en">
<head>
<meta charset="utf-8">
<title>Tarnwick – Auctions &amp; Real Estate</title>
<link href="https://fonts.googleapis.com/css2?family=Open+Sans:wght@400;600;700&display=swap" rel="stylesheet">
<style>
:root{
  --green:#0b8a3c;
  --green-dark:#06712f;
  --ink:#333;
  --muted:#7a7a7a;
  --band:#efefef;
  --panel:#f5f5f5;
  --line:#e2e2e2;
}
*{box-sizing:border-box;margin:0;padding:0}
html,body{width:895px;height:1200px;overflow:hidden;background:#fff;font-family:"Open Sans",sans-serif;color:var(--ink)}
.page{position:relative;width:895px;height:1200px}
.abs{position:absolute}
.brand{left:96px;top:30px;display:flex;align-items:center;gap:8px}
.brand-mark{width:16px;height:16px;border-radius:50%;background:var(--green)}
.brand-name{font-size:30px;font-weight:700;color:#1d1d1d;letter-spacing:1px}
.contact{right:97px;top:30px;text-align:right}
.contact .phone{font-size:15px;font-weight:700;color:var(--green)}
.contact .name{font-size:11px;color:#444;margin-top:3px}
.contact .mail{font-size:9px;color:#444;margin-top:4px}
.hero-band{left:0;top:94px;width:895px;height:303px;background:var(--band)}
.nav{left:97px;top:94px;width:701px;height:34px;background:var(--green);display:flex;align-items:center;justify-content:space-around;padding:0 8px}
.nav a{color:#fff;text-decoration:none;font-size:10.5px;font-weight:600}
.slide{left:97px;top:133px;width:701px;height:234px;background:linear-gradient(180deg,#5d9fe0 0%,#a9cdef 35%,#b9c2c0 55%,#5f9a3c 75%,#3f7e24 100%)}
.arrow-btn{width:38px;height:38px;border-radius:50%;background:rgba(255,255,255,.55);top:220px}
.welcome-title{left:0;width:895px;top:420px;text-align:center;font-size:11.5px;font-weight:700;color:var(--green)}
.welcome-text{left:97px;width:701px;top:447px;text-align:center;font-size:9px;line-height:18px;color:var(--muted)}
.auctions-band{left:0;top:546px;width:895px;height:322px;background:var(--band)}
.auctions-title{left:0;width:895px;top:559px;text-align:center;font-size:10.5px;font-weight:700;color:var(--green)}
.card{top:583px;width:164px}
.card .photo{height:81px}
.card h3{font-size:9px;font-weight:700;color:var(--green);line-height:18px;margin-top:9px}
.card p{font-size:7.5px;line-height:18px;color:#444}
.card .date{margin-top:2px;margin-bottom:4px}
.card .county{color:var(--green);font-weight:700}
.card .actions{display:flex;align-items:center;gap:8px;margin-top:6px}
.btn{background:var(--green);color:#fff;font-size:7.5px;font-weight:700;padding:6px 6px;display:inline-block}
.section-title{top:903px;font-size:10.5px;font-weight:700;color:var(--green)}
.video{left:97px;top:925px;width:224px;height:164px;background:#fff;border:1px solid var(--line)}
.video .label{position:absolute;left:36px;top:44px;font-size:24px;font-weight:700;color:#1d1d1d}
.video .caption{position:absolute;left:0;bottom:0;width:100%;height:44px;background:var(--green);color:#fff;font-size:7.5px;line-height:15px;padding:7px 16px}
.signup{left:335px;top:925px;width:224px;height:164px;background:var(--panel);padding:14px 13px}
.signup p,.testi p{font-size:7.5px;line-height:18px;color:var(--muted)}
.field{height:22px;background:#fff;border:1px solid #e8e8e8;font-size:7px;color:#bbb;padding:5px 8px;margin-top:9px}
.signup .btn{position:absolute;right:13px;bottom:14px;padding:7px 18px;background:var(--green-dark)}
.testi{left:575px;top:925px;width:223px;height:164px;background:var(--panel);padding:24px 13px}
.testi .who{text-align:right;margin-top:6px;font-size:10px;font-weight:700;color:var(--green)}
.testi .role{text-align:right;font-size:7.5px;color:var(--muted)}
.footer{left:0;top:1120px;width:895px;height:80px;background:var(--band)}
.foot-links{left:95px;top:1135px;font-size:9.5px;color:#444}
.foot-links span{margin:0 8px}
.copy{left:95px;top:1163px;font-size:9.5px;color:#444}
.social{top:1147px;width:24px;height:24px;border-radius:50%;background:#111}
</style>
</head>
<body>
<div class="page">
  <div class="abs brand"><span class="brand-mark"></span><span class="brand-name">TARNWICK</span></div>
  <div class="abs contact">
    <div class="phone">1-800-555-0148</div>
    <div class="name">Ned Garrow</div>
    <div class="mail">nedgarrow@tarnwick.com</div>
  </div>

  <div class="abs hero-band"></div>
  <nav class="abs nav">
    <a>Home</a><a>Auctions</a><a>Services</a><a>For Sale</a><a>About Us</a><a>Ned Videos</a><a>News &amp; Events</a><a>Contact Us</a>
  </nav>
  <div class="abs slide" role="img" aria-label="Slideshow photo of a single-storey house with palm trees and a green lawn"></div>
  <div class="abs arrow-btn" style="left:116px"><svg width="38" height="38"><path d="M22 11 L14 19 L22 27" stroke="#555" stroke-width="3" fill="none"/></svg></div>
  <div class="abs arrow-btn" style="left:739px"><svg width="38" height="38"><path d="M16 11 L24 19 L16 27" stroke="#555" stroke-width="3" fill="none"/></svg></div>

  <h2 class="abs welcome-title">WELCOME TO TARNWICK</h2>
  <p class="abs welcome-text">Lorem Ipsum is simply dummy text of the printing and typesetting industry. Lorem Ipsum has been the industry's standard dummy text ever since the 1500s, when an unknown printer took a galley of type and scrambled it to make a type specimen book. It has survived not only five centuries, but also the leap into electronic typesetting, remaining essentially unchanged. It was popularised in the 1960s with the release of Letraset sheets containing Lorem Ipsum passages, and more recently with desktop publishing software like Aldus PageMaker including versions of Lorem Ipsum.</p>

  <div class="abs auctions-band"></div>
  <svg class="abs" style="left:95px;top:556px" width="12" height="16"><path d="M9 2 L3 8 L9 14" stroke="var(--green)" stroke-width="2.5" fill="none"/></svg>
  <svg class="abs" style="left:786px;top:556px" width="12" height="16"><path d="M3 2 L9 8 L3 14" stroke="var(--green)" stroke-width="2.5" fill="none"/></svg>
  <h2 class="abs auctions-title">CURRENT AUCTIONS</h2>

  <div class="abs card" style="left:97px">
    <div class="photo" role="img" aria-label="Photo of an agent standing in front of a house" style="background:linear-gradient(180deg,#8fbde0,#cfd6d6 50%,#5e8a3e)"></div>
    <h3>Commercial Buildings and Lot-<br>Cedar Hollow, AR</h3>
    <p class="date">Jan 21, 2014 ,11am Eastern</p>
    <p>On Site &nbsp;: &nbsp;2817 Harlow Ave,<br>Cedar Hollow, AR 72015<br>Commercial Buildings and Lot - Great Road<br>Frontage on Harlow Avenue in<br>Cedar Hollow, AR. <span class="county">– Alder County</span></p>
    <div class="actions"><span class="btn">More Details</span><svg width="18" height="16"><rect x="1" y="3" width="14" height="11" fill="none" stroke="#333" stroke-width="1.5"/><path d="M3 12 L7 7 L10 10 L13 6" stroke="#333" fill="none"/></svg></div>
  </div>
  <div class="abs card" style="left:276px">
    <div class="photo" role="img" aria-label="Photo of a hand holding house keys before a home" style="background:linear-gradient(135deg,#d9a66a,#3a7fd0 60%,#1f5fb0)"></div>
    <h3>Commercial Buildings and Lot-<br>Cedar Hollow, AR</h3>
    <p class="date">Jan 21, 2014 ,11am Eastern</p>
    <p>On Site &nbsp;: &nbsp;2817 Harlow Ave,<br>Cedar Hollow, AR 72015<br>Commercial Buildings and Lot - Great Road<br>Frontage on Harlow Avenue in<br>Cedar Hollow, AR. <span class="county">– Alder County</span></p>
    <div class="actions"><span class="btn">More Details</span><svg width="18" height="16"><rect x="1" y="3" width="14" height="11" fill="none" stroke="#333" stroke-width="1.5"/><path d="M3 12 L7 7 L10 10 L13 6" stroke="#333" fill="none"/></svg></div>
  </div>
  <div class="abs card" style="left:455px">
    <div class="photo" role="img" aria-label="Photo of a row of suburban houses" style="background:linear-gradient(180deg,#8cc0ea,#c9cfd4 45%,#9aa3a8 70%,#6b9a4a)"></div>
    <h3>Commercial Buildings and Lot-<br>Cedar Hollow, AR</h3>
    <p class="date">Jan 21, 2014 ,11am Eastern</p>
    <p>On Site &nbsp;: &nbsp;2817 Harlow Ave,<br>Cedar Hollow, AR 72015<br>Commercial Buildings and Lot - Great Road<br>Frontage on Harlow Avenue in<br>Cedar Hollow, AR. <span class="county">– Alder County</span></p>
    <div class="actions"><span class="btn">More Details</span><svg width="18" height="16"><rect x="1" y="3" width="14" height="11" fill="none" stroke="#333" stroke-width="1.5"/><path d="M3 12 L7 7 L10 10 L13 6" stroke="#333" fill="none"/></svg></div>
  </div>
  <div class="abs card" style="left:634px">
    <div class="photo" role="img" aria-label="Photo of a brick ranch house among trees" style="background:linear-gradient(180deg,#5f8e46,#a9b8a0 45%,#8a5a44 65%,#4f8a2e)"></div>
    <h3>Commercial Buildings and Lot-<br>Cedar Hollow, AR</h3>
    <p class="date">Jan 21, 2014 ,11am Eastern</p>
    <p>On Site &nbsp;: &nbsp;2817 Harlow Ave,<br>Cedar Hollow, AR 72015<br>Commercial Buildings and Lot - Great Road<br>Frontage on Harlow Avenue in<br>Cedar Hollow, AR. <span class="county">– Alder County</span></p>
    <div class="actions"><span class="btn">More Details</span><svg width="18" height="16"><rect x="1" y="3" width="14" height="11" fill="none" stroke="#333" stroke-width="1.5"/><path d="M3 12 L7 7 L10 10 L13 6" stroke="#333" fill="none"/></svg></div>
  </div>

  <h2 class="abs section-title" style="left:97px">FEATURED VIDEO</h2>
  <h2 class="abs section-title" style="left:334px">E-MAIL SIGN UP</h2>
  <h2 class="abs section-title" style="left:575px">TESTIMONIALS</h2>

  <div class="abs video">
    <span class="label">TARNWICK</span>
    <svg style="position:absolute;left:94px;top:42px" width="40" height="40"><circle cx="20" cy="20" r="19" fill="#333" stroke="#fff" stroke-width="2"/><path d="M15 11 L29 20 L15 29 Z" fill="#fff"/></svg>
    <div class="caption">Lorem Ipsum is simply dummy text of the printing and typesetting industry.</div>
  </div>

  <div class="abs signup">
    <p>Lorem Ipsum is simply dummy text of the printing and typesetting industry. Lorem Ipsum has been the industry's standard dummy text</p>
    <div class="field">Enter Your Name</div>
    <div class="field">Enter Your E-mail</div>
    <span class="btn">SIGN UP</span>
  </div>

  <div class="abs testi">
    <p>Lorem Ipsum is simply dummy text of the printing and typesetting industry. Lorem Ipsum has been the industry's standard dummy text ever since the 1500s, when an unknown printer took a galley of type and scrambled it to make a type</p>
    <div class="who">Carl Benning</div>
    <div class="role">Tarnwick Customer</div>
  </div>

  <footer class="abs footer"></footer>
  <div class="abs foot-links">Home<span>|</span>Auctions<span>|</span>Services<span>|</span>For Sale<span>|</span>About Us<span>|</span>Ned Videos<span>|</span>News &amp; Events<span>|</span>Contact Us</div>
  <div class="abs copy">Copyright ©2013 Company Name &nbsp;&nbsp;- All rights reserved</div>
  <div class="abs social" style="left:714px"></div>
  <div class="abs social" style="left:743px"></div>
  <div class="abs social" style="left:772px"></div>
</div>
</body>
</html>
```